Cleaning Service Company In need of Good Web presence.

The company is a cleaning service company which provides professional staff and service for cleaning. This is a project to build a site that is both solid and a strong recognition of our organization. It is supposed to show quality, cleanliness, professionalism. The use of images and art for imagery is all good just to have a site that is consistent and solid. There might be a chance to make stationary, logo and business cars if someone feels they can build a brand that is consistent. The image we are going for is clean solid and to stand out. Finally stationary should not be expensive to print.

Current logo is attached and can be used or can be made more creative.

Target Market(s)

Corporate and Government entities, that will feel that this company has a brand that sets it apart from the rest. The company is new so the modification of the logo will not be an issue if a more solid brand come out of this project. The idea is to have a clean consistent product that stands our from others in terms of website, stationary, etc

Industry/Entity Type

Cleaning Service

Contact Information for Business Card

P.O.Box 51947
Riffa
Kingdom of Bahrain

Logo Text

Harbor Lane Services

Number of Pages Required

4 page

Font styles to use
Sans Serif

Colors
abd036
cadf82
eaf2ce
9bcb3b

Requirements
Must have
• Green Color to be used in order to stick to the name. Also the creativity and boldness in an elegant manner.
Nice to have
• Arabic name of company
• هاربر لين سرفسس ذ.م.م
• if cannot be put at least make a location should be chosen
• Also could be a bit of 3D given to the logo if it could stay elegent.
Should not have
• Should not show people cleaning.

```html
<!DOCTYPE html>
<html lang="en">
<head>
<meta charset="utf-8">
<title>Harbor Lane Services</title>
<link href="https://fonts.googleapis.com/css2?family=Open+Sans:wght@300;400;600;700&display=swap" rel="stylesheet">
<style>
:root{
  --green:#9bcb3b;
  --green-2:#abd036;
  --green-soft:#cadf82;
  --green-pale:#eaf2ce;
  --ink:#2b2b2b;
  --dark:#1f1f1f;
  --muted:#777;
  --line:#e2e2e2;
  --white:#fff;
}
*{box-sizing:border-box;margin:0;padding:0}
html,body{width:1200px;height:3188px;overflow:hidden}
body{font-family:"Open Sans",Arial,sans-serif;color:var(--ink);background:var(--white);position:relative}
.abs{position:absolute}

/* hero */
.hero{left:0;top:0;width:1200px;height:500px;background:radial-gradient(ellipse at 55% 45%,#8a8a8a 0%,#5c5c5c 45%,#3a3a3a 100%)}
.topbar{left:0;top:0;width:1200px;height:96px;background:linear-gradient(#1b1b1b,rgba(27,27,27,.55))}
.brand{left:40px;top:18px;display:flex;align-items:center;gap:12px}
.brand-mark{width:58px;height:58px;border-radius:50%;background:var(--green)}
.brand-name{font-weight:600;font-size:18px;color:var(--white)}
.nav{right:90px;top:58px;display:flex;gap:40px;font-size:13px;color:var(--white)}
.nav span.active{color:var(--green)}
.top-contact{right:90px;top:20px;display:flex;align-items:center;gap:18px;font-size:12px;color:#ddd}
.search{width:110px;height:22px;border:1px solid #aaa;border-radius:11px;padding-left:10px;font-size:11px;color:#aaa;line-height:20px}
.slide-arrow{top:258px;width:26px;height:26px;border-radius:50%;background:rgba(255,255,255,.35)}

/* info bar */
.infobar{left:0;top:500px;width:1200px;height:80px;background:var(--dark);display:flex}
.info{flex:1;display:flex;align-items:center;padding:0 36px;gap:16px;color:var(--white);border-right:1px solid #333;position:relative}
.info:last-child{border:none}
.info h4{font-size:14px;font-weight:600}
.info p{font-size:11px;color:#bbb;margin-top:3px}
.info .dot{position:absolute;right:36px;top:31px;width:18px;height:18px;border-radius:50%;background:var(--green)}

/* section titles */
.section-title{left:0;width:1200px;text-align:center;font-size:30px;font-weight:400;color:var(--ink);display:flex;justify-content:center;align-items:center;gap:12px}
.section-title .dash{width:28px;height:2px;background:#bbb}
.leaf{width:18px;height:18px}

/* what we do */
.service-list{left:80px;top:730px;width:330px}
.service-item{height:110px;border:1px solid var(--line);margin-bottom:2px;display:flex;gap:14px;padding:18px 16px;background:var(--white)}
.service-item.active{background:var(--green-pale);border-color:var(--green-soft)}
.service-icon{width:52px;height:52px;flex:none}
.service-item h5{font-size:13px;font-weight:600;color:#6a9a1a;margin-bottom:6px}
.service-item p{font-size:11px;color:var(--muted);line-height:1.5}
.card{top:730px;width:320px;height:340px;border:1px solid var(--line)}
.card .photo{height:128px}
.card .body{padding:14px 16px}
.card h5{font-size:13px;font-weight:600;margin-bottom:8px}
.card p{font-size:11px;color:var(--muted);line-height:1.5}
.btn-small{display:inline-block;margin-top:12px;background:var(--green-soft);color:var(--ink);font-size:11px;padding:5px 16px}

/* band */
.band{left:0;top:1136px;width:1200px;height:156px;background:linear-gradient(90deg,#abd036 0%,#cadf82 50%,#9bcb3b 100%)}
.band-label{position:absolute;left:80px;top:42px;display:flex;align-items:center;gap:10px;font-size:18px;font-weight:600;color:#2b3a10}
.band-text{position:absolute;left:118px;top:78px;width:560px;font-size:14px;color:#3a4a1a;line-height:1.5}
.join{position:absolute;left:822px;top:54px;width:260px;height:46px;border:2px solid var(--white);color:var(--white);font-size:24px;text-align:center;line-height:42px}

/* works */
.works{left:80px;top:1456px;width:1030px;height:352px;display:grid;grid-template-columns:330px 1fr 1fr;grid-template-rows:1fr 1fr;gap:20px}
.works .tall{grid-row:1/3}

/* booking */
.booking{left:0;top:1868px;width:1200px;height:444px;background:linear-gradient(100deg,#5f7fa8 0%,#b7c3cf 30%,#e5e9ec 55%,#d9dde0 100%)}
.form{left:580px;top:1912px;width:492px;height:280px;background:var(--green-pale);padding:24px 36px}
.form h3{display:flex;justify-content:center;align-items:center;gap:10px;font-size:22px;font-weight:400;margin-bottom:20px}
.row{display:flex;gap:20px;margin-bottom:12px}
.field{flex:1;height:28px;background:var(--white);font-size:10px;color:#aaa;padding:7px 10px}
.field.area{height:52px}
.submit{height:26px;background:var(--green-soft);text-align:center;font-size:12px;line-height:26px;margin-top:12px}

/* blog */
.post{top:2490px;width:320px}
.post .photo{height:212px}
.post h5{font-size:13px;font-weight:600;margin:16px 0 8px}
.post p{font-size:11px;color:var(--muted);line-height:1.5}
.meta{display:flex;gap:20px;font-size:10px;color:#999;margin-top:8px}

/* footer */
.footer{left:0;top:2900px;width:1200px;height:288px;background:var(--dark)}
.fcol{top:2960px;color:#ccc;font-size:12px;line-height:1.7}
.fcol h6{color:var(--white);font-size:13px;font-weight:600;margin-bottom:12px}
.fcol li{list-style:none;display:flex;align-items:center;gap:8px}
.fcol li::before{content:"";width:5px;height:5px;background:var(--green);border-radius:50%}
.news{display:flex}
.news .in{width:180px;height:30px;background:var(--white);font-size:10px;color:#999;padding:8px}
.news .go{width:30px;height:30px;background:var(--green)}
.copy{left:0;top:3140px;width:1200px;text-align:center;font-size:11px;color:#888;border-top:1px solid #333;padding-top:14px}
</style>
</head>
<body>

<!-- hero -->
<div class="abs hero" role="img" aria-label="Floor polishing machine on a tiled floor seen from above"></div>
<div class="abs topbar"></div>
<div class="abs brand"><div class="brand-mark"></div><div class="brand-name">Harbor Lane Services</div></div>
<div class="abs top-contact"><span>(800) 555 0142</span><div class="search">Search</div></div>
<div class="abs nav"><span class="active">Home</span><span>About Us</span><span>Services</span><span>Contact Us</span></div>
<div class="abs slide-arrow" style="left:20px"></div>
<div class="abs slide-arrow" style="right:20px"></div>

<!-- info bar -->
<div class="abs infobar">
  <div class="info">
    <svg width="34" height="34" viewBox="0 0 34 34" fill="none" stroke="#fff" stroke-width="2"><circle cx="17" cy="17" r="14"/><path d="M17 9v8l6 4"/></svg>
    <div><h4>Opening Hours</h4><p>Mon-Fri 8:00 AM - 9:00 PM</p></div><span class="dot"></span>
  </div>
  <div class="info">
    <svg width="34" height="34" viewBox="0 0 34 34" fill="none" stroke="#fff" stroke-width="2"><path d="M4 17L17 5l13 12"/><path d="M8 14v15h18V14"/><path d="M14 29v-8h6v8"/></svg>
    <div><h4>Address</h4><p>48 Harbor Road, Riffa</p></div><span class="dot"></span>
  </div>
  <div class="info">
    <svg width="34" height="34" viewBox="0 0 34 34" fill="none" stroke="#fff" stroke-width="2"><rect x="10" y="3" width="14" height="28" rx="2"/><path d="M15 26h4"/></svg>
    <div><h4>Phone</h4><p>(800) 555 0142</p></div><span class="dot"></span>
  </div>
</div>

<!-- what we do -->
<h2 class="abs section-title" style="top:660px">
  <svg class="leaf" viewBox="0 0 18 18"><path d="M2 16C2 6 8 2 16 2c0 8-4 14-14 14z" fill="#9bcb3b"/></svg>What We Do<span class="dash"></span>
</h2>
<div class="abs service-list">
  <div class="service-item active">
    <svg class="service-icon" viewBox="0 0 52 52" fill="none" stroke="#6a9a1a" stroke-width="2"><path d="M14 40h24M20 40V18h12v22M24 18v-8h4v8"/></svg>
    <div><h5>GENERAL CLEANING</h5><p>When we clean a home or office we take care of every corner in full detail.</p></div>
  </div>
  <div class="service-item">
    <svg class="service-icon" viewBox="0 0 52 52" fill="none" stroke="#6a9a1a" stroke-width="2"><rect x="12" y="12" width="28" height="30"/><path d="M18 20h4M30 20h4M18 28h4M30 28h4M24 42v-6h4v6"/></svg>
    <div><h5>COMMERCIALS CLEANING</h5><p>When we clean a workplace we keep each desk and floor neat for all staff.</p></div>
  </div>
  <div class="service-item">
    <svg class="service-icon" viewBox="0 0 52 52" fill="none" stroke="#6a9a1a" stroke-width="2"><path d="M14 38l16-16M30 22a7 7 0 1 0 6-10l-4 4-4-2-2-4 4-4"/></svg>
    <div><h5>MAINTENANCE SERVICES</h5><p>When we care for a site we fix small faults and keep it safe for years.</p></div>
  </div>
</div>
<div class="abs card" style="left:440px">
  <div class="photo" role="img" aria-label="Hands wiping a kitchen counter with a blue cloth" style="background:linear-gradient(135deg,#6fa3c8,#c9d6de)"></div>
  <div class="body"><h5>GREEN CLEAN SERVICES</h5><p>When we clean a property we use safe products that protect people and the planet every day.</p><span class="btn-small">Learn more</span></div>
</div>
<div class="abs card" style="left:790px">
  <div class="photo" role="img" aria-label="Team tidying a bright apartment living room" style="background:linear-gradient(135deg,#d8d0bf,#8fae5a)"></div>
  <div class="body"><h5>APARTMENT CLEANING</h5><p>When we clean an apartment we leave every room fresh, bright and ready for living.</p><span class="btn-small">Learn more</span></div>
</div>

<!-- band -->
<div class="abs band">
  <div class="band-label"><svg class="leaf" viewBox="0 0 18 18"><path d="M2 16C2 6 8 2 16 2c0 8-4 14-14 14z" fill="#2b3a10"/></svg>CLEANING SERVICES</div>
  <p class="band-text">There are many variations of passages of lorem ipsum available, but the majority have suffered alteration in some form.</p>
  <div class="join">Join Us Now</div>
</div>

<!-- works -->
<h2 class="abs section-title" style="top:1380px">
  <svg class="leaf" viewBox="0 0 18 18"><path d="M2 16C2 6 8 2 16 2c0 8-4 14-14 14z" fill="#9bcb3b"/></svg>Our Works<span class="dash"></span>
</h2>
<div class="abs works">
  <div class="tall" role="img" aria-label="Gloved hands holding a pink spray bottle" style="background:linear-gradient(135deg,#7fb2d6,#e6eef3)"></div>
  <div role="img" aria-label="Cleaning supplies on a window sill" style="background:linear-gradient(135deg,#a9c86a,#e0e7d2)"></div>
  <div role="img" aria-label="Mop resting in a bright hallway" style="background:linear-gradient(135deg,#c9cfc9,#8fa79a)"></div>
  <div role="img" aria-label="Spray bottle and sponge on a blue surface" style="background:linear-gradient(135deg,#79b7da,#b8d86a)"></div>
  <div role="img" aria-label="Mop and bucket on a wooden floor" style="background:linear-gradient(135deg,#e2c78f,#f0b84a)"></div>
</div>

<!-- booking -->
<div class="abs booking" role="img" aria-label="Bucket of colourful cleaning tools and gloves"></div>
<div class="abs form">
  <h3><svg class="leaf" viewBox="0 0 18 18"><path d="M2 16C2 6 8 2 16 2c0 8-4 14-14 14z" fill="#9bcb3b"/></svg>Service Booking</h3>
  <div class="row"><div class="field">Name</div><div class="field">Email</div></div>
  <div class="row"><div class="field">Phone</div><div class="field">Service</div></div>
  <div class="field area">Message</div>
  <div class="submit">Submit</div>
</div>

<!-- blog -->
<h2 class="abs section-title" style="top:2412px">
  <svg class="leaf" viewBox="0 0 18 18"><path d="M2 16C2 6 8 2 16 2c0 8-4 14-14 14z" fill="#9bcb3b"/></svg>Recent Blog<span class="dash"></span>
</h2>
<div class="abs post" style="left:88px">
  <div class="photo" role="img" aria-label="Cleaner wiping a white kitchen surface" style="background:linear-gradient(135deg,#8ec0de,#eef2f4)"></div>
  <h5>LOREM IPSUM DOLOR</h5><p>It is a long established fact that a reader will be distracted by readable content of a page.</p>
  <div class="meta"><span>20 Aug 2017</span><span>2 comments</span></div>
</div>
<div class="abs post" style="left:440px">
  <div class="photo" role="img" aria-label="Yellow gloves cleaning a sink tap" style="background:linear-gradient(135deg,#b9c6cf,#f1d24a)"></div>
  <h5>LOREM IPSUM DOLOR</h5><p>It is a long established fact that a reader will be distracted by readable content of a page.</p>
  <div class="meta"><span>20 Aug 2017</span><span>2 comments</span></div>
</div>
<div class="abs post" style="left:790px">
  <div class="photo" role="img" aria-label="Basket of cleaning products and gloves" style="background:linear-gradient(135deg,#a7cf5a,#f2e37a)"></div>
  <h5>LOREM IPSUM DOLOR</h5><p>It is a long established fact that a reader will be distracted by readable content of a page.</p>
  <div class="meta"><span>20 Aug 2017</span><span>2 comments</span></div>
</div>

<!-- footer -->
<div class="abs footer"></div>
<div class="abs fcol" style="left:88px;width:240px">
  <h6>About Us</h6>
  <p>Harbor Lane Services brings trained staff and careful work to offices, homes and public sites across the kingdom every day.</p>
</div>
<div class="abs fcol" style="left:400px">
  <h6>Quick Links</h6>
  <ul><li>Home</li><li>About us</li><li>Services</li><li>Contact us</li></ul>
</div>
<div class="abs fcol" style="left:610px">
  <h6>Services</h6>
  <ul><li>general cleaning</li><li>commercials cleaning</li><li>maintenance services</li></ul>
</div>
<div class="abs fcol" style="left:860px">
  <h6>Subscribe Newsletter</h6>
  <div class="news"><div class="in">Enter your email</div><div class="go"></div></div>
</div>
<div class="abs copy">harborlaneservices.com &copy; 2017. All rights reserved</div>

</body>
</html>
```